KLV Plant Services

We are a heavy diesel mechanical business with additional air con certificates, remapping engine rebuilt

Contact Information for Business Card

Company Name, Director Name, Managing Director, Contact details, email and website

Font styles to use
Serif
Script

```html
<!DOCTYPE html>
<html lang="en">
<head>
<meta charset="utf-8">
<title>KLV Plant Services – Business Card</title>
<link href="https://fonts.googleapis.com/css2?family=Mulish:wght@400;700;800&family=Questrial&display=swap" rel="stylesheet">
<style>
  :root{
    --bg:#2b2b2e;
    --card:#ffffff;
    --navy:#25256e;
    --ink:#1e1e24;
    --grey:#6a6a72;
    --band-top:#6f73ad;
    --band-bottom:#9b97bd;
    --band-edge:#dfe0ee;
  }
  *{margin:0;padding:0;box-sizing:border-box}
  html,body{width:1200px;height:900px;overflow:hidden;background:var(--bg)}
  .stage{position:relative;width:1200px;height:900px}
  .card{
    position:absolute;left:280px;width:640px;height:366px;
    background:var(--card);overflow:hidden;
    box-shadow:0 10px 30px rgba(0,0,0,.45);
    font-family:"Mulish",sans-serif;color:var(--ink);
  }
  .card--services{top:50px}
  .card--contact{top:484px}
  .band{position:absolute;inset:0;width:100%;height:100%}
  .content{position:absolute;inset:0}

  .brand{
    position:absolute;display:flex;align-items:center;gap:10px;
    font-family:"Mulish",sans-serif;font-weight:800;color:var(--navy);
    white-space:nowrap;
  }
  .brand__dot{width:14px;height:14px;border-radius:50%;background:var(--navy)}
  .card--services .brand{left:50%;top:34px;transform:translateX(-50%);font-size:26px}
  .card--contact .brand{right:40px;top:40px;font-size:28px}

  .services{position:absolute;left:0;right:0;top:118px;text-align:center}
  .services__title{font-weight:700;font-size:19px;letter-spacing:.5px;margin-bottom:14px}
  .services__list{list-style:none;font-weight:800;font-size:15.5px;line-height:1.62}

  .person{position:absolute;left:40px;top:160px}
  .person__name{font-weight:800;font-size:22px;color:var(--navy);letter-spacing:.3px;text-transform:uppercase}
  .person__role{font-family:"Questrial",sans-serif;font-size:20px;color:var(--grey);margin-top:2px}

  .address{
    position:absolute;right:40px;top:150px;text-align:right;
    font-family:"Questrial",sans-serif;font-size:19px;line-height:1.3;color:#3a3a44;
  }
  .contacts{position:absolute;left:40px;bottom:28px;list-style:none;
    font-family:"Questrial",sans-serif;font-size:21px;color:#26262e;line-height:1.45}
  .contacts li{display:flex;align-items:center;gap:10px}
  .contacts svg{width:18px;height:18px;flex:none}
</style>
</head>
<body>
<main class="stage">

  <section class="card card--services">
    <svg class="band" viewBox="0 0 640 366" preserveAspectRatio="none" aria-hidden="true">
      <defs>
        <linearGradient id="bandFillA" x1="0" y1="0" x2="0" y2="1">
          <stop offset="0" stop-color="var(--band-top)"/>
          <stop offset="1" stop-color="var(--band-bottom)"/>
        </linearGradient>
      </defs>
      <path fill="var(--band-edge)" d="M0 208 L40 196 L70 170 L120 160 L150 134 L200 128 L240 108 L300 104 L340 86 L390 84 L430 64 L480 62 L520 46 L580 44 L640 30 L640 366 L0 366 Z"/>
      <path fill="url(#bandFillA)" d="M0 214 L45 202 L72 178 L122 168 L152 142 L205 136 L242 116 L302 112 L342 94 L392 92 L432 72 L482 70 L522 54 L582 52 L640 38 L640 366 L0 366 Z"/>
    </svg>
    <div class="content">
      <div class="brand"><span class="brand__dot"></span>KLV Plant Services</div>
      <div class="services">
        <h2 class="services__title">OUR SERVICES</h2>
        <ul class="services__list">
          <li>Civil And Mining Equipment Repair And Maintenance</li>
          <li>Mobile And Fixed Plant Services / Component Rebuilds</li>
          <li>Crushing Equipment Repair / Road Transport Maintenance / Diagnostics</li>
          <li>Ecu Remapping / Auto Electrics / Air Conditioning</li>
          <li>Fabrication And Boiler Making / Labour Hire / Specialised Tool Hire</li>
        </ul>
      </div>
    </div>
  </section>

  <section class="card card--contact">
    <svg class="band" viewBox="0 0 640 366" preserveAspectRatio="none" aria-hidden="true">
      <defs>
        <linearGradient id="bandFillB" x1="0" y1="0" x2="0" y2="1">
          <stop offset="0" stop-color="var(--band-top)"/>
          <stop offset="1" stop-color="var(--band-bottom)"/>
        </linearGradient>
      </defs>
      <path fill="var(--band-edge)" d="M0 276 L50 262 L90 232 L150 226 L190 200 L250 196 L290 172 L350 170 L390 150 L450 146 L490 124 L560 120 L600 100 L640 96 L640 366 L0 366 Z"/>
      <path fill="url(#bandFillB)" d="M0 282 L52 270 L92 240 L152 234 L192 208 L252 204 L292 180 L352 178 L392 158 L452 154 L492 132 L562 128 L602 108 L640 104 L640 366 L0 366 Z"/>
    </svg>
    <div class="content">
      <div class="brand"><span class="brand__dot"></span>KLV Plant Services</div>
      <div class="person">
        <p class="person__name">Liam Hartley</p>
        <p class="person__role">Managing Director</p>
      </div>
      <address class="address">48 Harlow Road<br>Kelvin Park<br>WA 6061, Australia</address>
      <ul class="contacts">
        <li>
          <svg viewBox="0 0 24 24" aria-hidden="true"><path fill="#26262e" d="M6.6 10.8a15 15 0 0 0 6.6 6.6l2.2-2.2c.3-.3.7-.4 1-.2 1.1.4 2.3.6 3.6.6.6 0 1 .4 1 1V20c0 .6-.4 1-1 1A17 17 0 0 1 3 4c0-.6.4-1 1-1h3.5c.6 0 1 .4 1 1 0 1.3.2 2.5.6 3.6.1.3 0 .7-.2 1z"/></svg>
          0400 362 915
        </li>
        <li>
          <svg viewBox="0 0 24 24" aria-hidden="true"><path fill="#26262e" d="M2 5h20v14H2z"/><path fill="none" stroke="#fff" stroke-width="1.6" d="M2.5 5.5 12 13l9.5-7.5"/></svg>
          admin@klvplantservices.net
        </li>
        <li>
          <svg viewBox="0 0 24 24" aria-hidden="true"><g fill="none" stroke="#26262e" stroke-width="1.6"><circle cx="12" cy="12" r="9"/><ellipse cx="12" cy="12" rx="4" ry="9"/><path d="M3 12h18M5 7h14M5 17h14"/></g></svg>
          www.klvplantservices.net
        </li>
      </ul>
    </div>
  </section>

</main>
</body>
</html>
```